Hörbuchcover
Zielgruppe
Spiritueller Hörbuchverlag für ganzheitliche Gesundheit, Glück und Wohlstand.
Aufgabenstellung
Benötigt wird ein schönes quadratisches Cover, 2400x2400 mindestens 72dpi für ein Hörbuchcover.
Auf dem Cover soll eine gelb/orange Rose zu in Form einer Blüte zu sehen sein.
Titel: Goldener Pfad
Untertitel: Emotionen sind der Schlüssel für Gesundheit, Energie & Lebensfreude
Autorenname: Dr. med. Katrin Wollberg
Das Velmira Logo soll unten mittig sitzen.
Es folgen weiterer Hörbücher von dieser Autorin und es wäre gut wenn man die folgenden Cover in einem ähnlichen Stil halten könnte. Ein harmonisches und gut zu erkennendes Design mit hohem Wiedererkennungseffekt. Ich freue mich auf kreative Designvorschläge.
Auf velmira.de kann man sehen wo das Logo sitzen soll.
Herzliche Grüße - Jonas

```html
<!DOCTYPE html>
<html lang="de">
<head>
<meta charset="utf-8">
<title>Goldener Pfad – Hörbuchcover</title>
<link rel="stylesheet" href="https://fonts.googleapis.com/css2?family=Marcellus&family=Questrial&display=swap">
<style>
  :root {
    --ink: #0d0b08;
    --cream: #fff6d2;
    --butter: #ffe58a;
    --gold: #ffd23a;
    --amber: #f9b21c;
    --orange: #f39a14;
    --petal: #fff3c4;
  }
  * { margin: 0; padding: 0; box-sizing: border-box; }
  html, body { width: 1200px; height: 1200px; overflow: hidden; background: var(--cream); }
  .cover {
    position: relative;
    width: 1200px;
    height: 1200px;
    overflow: hidden;
    color: var(--ink);
    font-family: "Questrial", sans-serif;
  }
  .backdrop {
    position: absolute;
    inset: 0;
    background:
      radial-gradient(ellipse at 12% 28%, #fffbe8 0%, rgba(255,246,210,0) 40%),
      radial-gradient(ellipse at 30% 85%, var(--gold) 0%, rgba(255,210,58,0) 55%),
      linear-gradient(160deg, var(--butter) 0%, var(--cream) 28%, #ffe070 62%, var(--gold) 100%);
  }
  .rose-art {
    position: absolute;
    left: 600px;
    top: 60px;
    width: 1140px;
    height: 1140px;
    border-radius: 50%;
    background:
      radial-gradient(circle at 50% 52%,
        var(--amber) 0%,
        var(--orange) 6%,
        var(--gold) 14%,
        var(--petal) 22%,
        var(--gold) 30%,
        var(--amber) 38%,
        var(--petal) 46%,
        var(--gold) 55%,
        rgba(255,229,138,0.7) 64%,
        rgba(255,240,190,0) 72%);
  }
  .author {
    position: absolute;
    top: 86px;
    left: 0;
    width: 1136px;
    text-align: center;
    font-size: 43px;
    letter-spacing: 2px;
  }
  .title {
    position: absolute;
    top: 166px;
    left: 0;
    width: 1160px;
    text-align: center;
    font-family: "Marcellus", serif;
    font-weight: 400;
    font-size: 152px;
    line-height: 161px;
    letter-spacing: 2px;
    text-transform: uppercase;
  }
  .subtitle {
    position: absolute;
    top: 496px;
    left: 0;
    width: 1132px;
    text-align: center;
    font-size: 44px;
    line-height: 58px;
    letter-spacing: 3px;
  }
  .publisher {
    position: absolute;
    top: 944px;
    left: 449px;
    width: 350px;
    text-align: center;
  }
  .publisher-dot {
    display: block;
    width: 112px;
    height: 112px;
    margin: 0 auto 12px;
    border: 10px solid var(--ink);
    border-radius: 50%;
  }
  .publisher-name {
    font-size: 58px;
    letter-spacing: 9px;
    text-indent: 9px;
    line-height: 1;
    text-transform: uppercase;
    font-weight: 400;
  }
</style>
</head>
<body>
  <main class="cover">
    <div class="backdrop" aria-hidden="true"></div>
    <div class="rose-art" role="img" aria-label="Foto einer geöffneten gelb-orangen Rosenblüte, angeschnitten am rechten Rand"></div>
    <p class="author">DR. MED. KATRIN WOLLBERG</p>
    <h1 class="title">Goldener<br>Pfad</h1>
    <p class="subtitle">Emotionen sind der Schlüssel für<br>Gesundheit, Energie &amp; Lebensfreude</p>
    <div class="publisher">
      <span class="publisher-dot" aria-hidden="true"></span>
      <p class="publisher-name">Velmira</p>
    </div>
  </main>
</body>
</html>
```